Sunset Harbor Living Web Page

We need a web page design that has two intro pages - first being a 'home page', then a link to the second page that has the 'content tabs' and a 'call to action' (see below).

The business helps people that wish to retire to S.E.Asia (Thailand, Malaysia, Indonesia,The Philippines etc) - to enjoy the lifestyle and the remaining years of their lives. What attracts S.E.Asia to many people is the lower cost, the atmoshpere and beauty of the tropics and the vibrancy of the various countries.

People that are wishing to make the most of their retirement and are adventurous at a great bargain compared to the cost of their own countries will be interested.

We help them achieve this - visa, financials (tax, gov't payments etc), introduce them to the right people for property, clubs, retirement facilities, insurance and so forth.

Therefore we are providing an extremely wide ranging service and this site will provide broad but general information only - with a call to action to come and see us for more specific information and how we can help them specifically.

This site will be predominantly for travel and lifestyle, it will be linked with another financial services (financial planning) site later down the track.

The colour scheme is dark green and blue - as per the attached logo design. Photos and background just think lifestyle and S.E.Asia - beaches/mountains/water/recreational activities for retirees.

Target market is mostly those coming up to retirement to those that are already retired. But we also expect to have some interest with younger people that would like to find out more and plan for the future. So a broad age group but I would say mostly 40-70 yrs old.

On the first (Home) page we would like our company name 'Sunset Harbor Living', our logo (which will be on all pages) and a statement such as: “Imagine a retirement where your dreams are brought to life, and you have never felt more alive. Let us show you how”. Then a link to the second page.

We would like an uncluttered site. On the second (contents) page the tabs would be:

- Visa
- Property
- Financials
- Travel
- Insurance & Healthcare
- Medical Tourism
- Cost of living
- Weekly Blogs and articles
- Sunset Harbor Living story

We would also like a call to action on the second page - asking them to leave their contact details if they wish to learn more or sign up to our weekly newsletter/blog.

We are open to suggestions and your imaginations.

Thank you
Malcolm

Font styles to use
Serif
Script

Colors
0255a3
3377b5
00a990
9bcb3c
abd036
33b8a4
85abd2
cadf82
86cfc6

Requirements
Must have
• I have been asked by the web designer to receive a 'Web Font' so that we can 'get off of Zentrofy'. Hope that makes sense.

```html
<!DOCTYPE html>
<html lang="en">
<head>
<meta charset="utf-8">
<title>Sunset Harbor Living</title>
<link rel="stylesheet" href="https://fonts.googleapis.com/css2?family=Raleway:wght@400;500;600&family=Open+Sans:wght@400;700&display=swap">
<style>
  :root {
    --brand-blue: #0255a3;
    --brand-green: #9bcb3c;
    --brand-teal: #00a990;
    --footer-blue: #235f9b;
    --nav-text: #2b2b2b;
    --white: #ffffff;
    --border-grey: #cfcfcf;
    --muted: #9a9a9a;
  }
  * { box-sizing: border-box; margin: 0; padding: 0; }
  html, body { width: 1200px; height: 681px; overflow: hidden; }
  body { position: relative; font-family: 'Raleway', sans-serif; background: var(--white); }

  .top-strip {
    position: absolute; left: 0; top: 0; width: 1200px; height: 3px;
    background: linear-gradient(90deg, #85abd2, var(--brand-green) 50%, var(--brand-blue));
    z-index: 4;
  }
  .site-header {
    position: absolute; left: 0; top: 0; width: 1200px; height: 91px;
    background: var(--white); z-index: 3;
    box-shadow: 0 2px 4px rgba(0,0,0,0.25);
  }
  .brand-badge {
    position: absolute; left: 90px; top: -9px; width: 146px; height: 146px;
    border-radius: 50%; background: var(--white); z-index: 5;
    box-shadow: 0 3px 5px rgba(0,0,0,0.3);
    display: flex; align-items: center; justify-content: center; text-align: center;
  }
  .brand-name {
    font-family: 'Raleway', sans-serif; font-weight: 600; font-size: 18px;
    line-height: 21px; color: var(--brand-blue); padding-top: 14px;
  }
  .search-box {
    position: absolute; left: 753px; top: 14px; width: 228px; height: 29px;
    border: 1px solid var(--border-grey); display: flex; align-items: center;
    justify-content: space-between; padding: 0 10px 0 12px;
    font-size: 13px; color: #666;
  }
  .sign-in {
    position: absolute; left: 1003px; top: 20px; display: flex; align-items: center; gap: 12px;
    color: var(--brand-green); font-weight: 500; font-size: 13px;
  }
  .main-nav {
    position: absolute; right: 99px; top: 61px; display: flex; gap: 13px;
    font-size: 13px; font-weight: 500; color: var(--nav-text);
  }
  .main-nav .is-active { color: var(--brand-green); }

  .hero {
    position: absolute; left: 0; top: 91px; width: 1200px; height: 520px;
    background:
      linear-gradient(180deg, #2f6fb0 0%, #6f9fc8 22%, #3f6e3a 40%, #4e7f45 60%, #5fbfae 78%, #7fd0bf 100%);
  }
  .hero-headline {
    position: absolute; left: 0; top: 150px; width: 1200px; text-align: center;
    color: var(--white); font-weight: 600; font-size: 33px; line-height: 46px;
    text-shadow: 0 2px 6px rgba(0,0,0,0.45);
  }
  .hero-cta {
    position: absolute; left: 483px; top: 312px; width: 235px; height: 49px;
    background: var(--brand-green); border: 2px solid var(--white);
    color: var(--white); font-family: 'Open Sans', sans-serif; font-weight: 700;
    font-size: 15px; display: flex; align-items: center; justify-content: center;
    text-decoration: none; letter-spacing: 0.2px;
  }
  .slide-dots { position: absolute; left: 519px; top: 466px; display: flex; gap: 6px; }
  .slide-dots span { width: 36px; height: 8px; border-radius: 4px; background: var(--white); }
  .slide-dots .is-current { background: var(--brand-green); }

  .site-footer {
    position: absolute; left: 0; top: 611px; width: 1200px; height: 70px;
    background: var(--footer-blue);
  }
  .copyright {
    position: absolute; left: 99px; top: 26px; color: var(--white);
    font-family: 'Open Sans', sans-serif; font-size: 12px;
  }
  .social-links { position: absolute; left: 944px; top: 17px; display: flex; gap: 5px; }
  .social-links span {
    width: 35px; height: 35px; border-radius: 50%;
    background: var(--white); border: 2px solid var(--footer-blue);
    box-shadow: 0 0 0 1.5px var(--white);
  }
</style>
</head>
<body>
  <div class="top-strip"></div>

  <header class="site-header">
    <div class="brand-badge"><div class="brand-name">Sunset Harbor<br>Living</div></div>

    <div class="search-box">
      <span>Search</span>
      <svg width="13" height="13" viewBox="0 0 13 13" aria-hidden="true">
        <circle cx="5.5" cy="5.5" r="4.3" fill="none" stroke="#bbb" stroke-width="1.8"/>
        <line x1="8.6" y1="8.6" x2="12" y2="12" stroke="#bbb" stroke-width="2"/>
      </svg>
    </div>

    <div class="sign-in">
      <svg width="11" height="14" viewBox="0 0 11 14" aria-hidden="true">
        <path d="M2.5 6V4a3 3 0 0 1 6 0v2" fill="none" stroke="#9bcb3c" stroke-width="1.8"/>
        <rect x="0" y="6" width="11" height="8" rx="1" fill="#9bcb3c"/>
      </svg>
      <span>User Sign in</span>
    </div>

    <nav class="main-nav">
      <span class="is-active">Home</span>
      <span>Visa</span>
      <span>Property</span>
      <span>Financials</span>
      <span>Travel</span>
      <span>Insurance &amp; Healthcare</span>
      <span>Medical Tourism</span>
      <span>Cost of living</span>
      <span>Blogs &amp; articles</span>
      <span>Story</span>
      <span>Contact</span>
    </nav>
  </header>

  <section class="hero" role="img" aria-label="Tropical bay with limestone cliffs, turquoise water and longtail boats">
    <h1 class="hero-headline">Imagine a retirement where your dreams<br>are brought to life, and you have never felt more<br>alive. Let us show you how</h1>
    <a class="hero-cta" href="#">GET MORE INFORMATION</a>
    <div class="slide-dots"><span class="is-current"></span><span></span><span></span><span></span></div>
  </section>

  <footer class="site-footer">
    <p class="copyright">Copyright © 2016 , Sunset Harbor Living. All rights reserved.</p>
    <div class="social-links"><span></span><span></span><span></span><span></span></div>
  </footer>
</body>
</html>
```